High-end construction company needs a business card design

We need a modern looking business card that draws people in, is memorable and looks so good people will want to sick it on their fridges.
On the first side what is needed are:
Logo
My name - Tomasz Brelwik
Title - Managing Director
Website - www.varkelt.co.uk
Email - tomasz@varkelt.co.uk
Telephone - 020 5194 6281
Mobile - 07845139072
On the back side was is needed is a list of all the services we provide:
-Kitchen Renovations
-Bathroom Renovations
-House Renovations
-Garage Conversions
-Extensions
-Loft Conversions
-Conservatories
-Carpentry
-Tiling
-Electrical
-Plumbing & Heating
-Bricklaying
-Landscaping
-Decorating
-Plastering
We would like the colours to be the same shades as on the logo with grey or black for the words.
Target Market(s)
Anyone who needs building work done
Contact Information for Business Card
This business card is for a construction company which strives to deliver excellent service and quality.
The look and feel of the card should represent this.
Requirements
Must have
- On the first side what is needed are:
Logo
My name - Tomasz Brelwik
Title - Managing Director
Website - www.varkelt.co.uk
Email - tomasz@varkelt.co.uk
Telephone - 020 5194 6281
Mobile - 07845139072
Nice to have
- Cool looking features

```html
<!DOCTYPE html>
<html lang="en">
<head>
<meta charset="utf-8">
<title>Varkelt Construction Ltd – Business Card</title>
<link rel="stylesheet" href="https://fonts.googleapis.com/css2?family=Open+Sans:wght@400;700&display=swap">
<style>
  :root {
    --green-dark: #4a8c3f;
    --green-light: #77bd43;
    --green-pale: #c6e2b4;
    --ink: #1e1e1e;
    --page: #ffffff;
  }
  * { margin: 0; padding: 0; box-sizing: border-box; }
  html, body { width: 1000px; height: 1200px; overflow: hidden; background: var(--page); }
  body { position: relative; font-family: "Open Sans", Arial, sans-serif; color: var(--ink); }

  .card { position: absolute; left: 98px; width: 804px; height: 461px; background: var(--green-light); border: 5px solid var(--green-dark); overflow: hidden; }
  .card--front { top: 117px; }
  .card--back { top: 622px; left: 97px; width: 804px; height: 461px; }

  .front-art { position: absolute; left: -5px; top: -5px; width: 804px; height: 461px; }

  .brand { position: absolute; left: 58px; top: 240px; width: 232px; text-align: center; font-weight: 700; color: var(--ink); }
  .brand__name { font-size: 50px; line-height: 1; letter-spacing: 1px; }
  .brand__sub { font-size: 14.5px; letter-spacing: 1.6px; margin-top: 4px; }

  .person { position: absolute; left: 382px; top: 72px; }
  .person__name { font-size: 27px; font-weight: 700; letter-spacing: 2px; line-height: 1.1; }
  .person__title { font-size: 19px; letter-spacing: 1px; margin-top: 3px; }

  .contact { position: absolute; left: 0; top: 0; list-style: none; }
  .contact__item { position: absolute; display: flex; align-items: center; white-space: nowrap; font-size: 22px; letter-spacing: 3.6px; }
  .contact__icon { position: absolute; width: 22px; height: 22px; }

  .services-band { position: absolute; left: 0; top: 79px; width: 100%; height: 40px;
    background: linear-gradient(90deg, var(--green-dark) 0%, var(--green-pale) 50%, var(--green-dark) 100%); }
  .services-band__title { text-align: center; font-size: 27px; font-weight: 700; letter-spacing: 1px; line-height: 40px; }

  .services { position: absolute; top: 150px; list-style: none; }
  .services--left { left: 101px; }
  .services--right { left: 450px; }
  .services li { position: relative; padding-left: 22px; font-size: 21.5px; line-height: 30.5px; letter-spacing: 0.3px; white-space: nowrap; }
  .services li::before { content: ""; position: absolute; left: 0; top: 9px; width: 13px; height: 13px; border-radius: 50%; background: var(--ink); }
</style>
</head>
<body>

<section class="card card--front">
  <svg class="front-art" viewBox="98 117 804 461" aria-hidden="true">
    <defs>
      <linearGradient id="nameBand" x1="0" x2="1">
        <stop offset="0" stop-color="#4a8c3f"/>
        <stop offset="0.5" stop-color="#c6e2b4"/>
        <stop offset="1" stop-color="#4a8c3f"/>
      </linearGradient>
      <linearGradient id="crescent" x1="380" x2="490" y1="0" y2="0" gradientUnits="userSpaceOnUse">
        <stop offset="0" stop-color="#4a8c3f"/>
        <stop offset="1" stop-color="#cfe4c2"/>
      </linearGradient>
    </defs>
    <rect x="395" y="183" width="507" height="79" fill="url(#nameBand)"/>
    <path d="M98,117 L285,122 C430,170 505,280 488,360 C470,450 390,530 285,572 L98,578 Z" fill="url(#crescent)"/>
    <path d="M98,117 L285,122 C400,180 460,280 445,360 C430,440 370,520 285,572 L98,578 Z" fill="#4a8c3f"/>
  </svg>

  <div class="brand">
    <div class="brand__name">VARKELT</div>
    <div class="brand__sub">CONSTRUCTION LTD</div>
  </div>

  <div class="person">
    <h1 class="person__name">TOMASZ BRELWIK</h1>
    <p class="person__title">MANAGING DIRECTOR</p>
  </div>

  <ul class="contact">
    <li class="contact__item" style="left:382px; top:154px;">
      <svg class="contact__icon" style="left:-36px; top:2px;" viewBox="0 0 22 22" aria-label="Mobile"><rect x="5" y="1" width="12" height="20" rx="2" fill="#1e1e1e"/><rect x="7.5" y="4" width="7" height="12" fill="#77bd43"/></svg>
      07845139072
    </li>
    <li class="contact__item" style="left:404px; top:198px;">
      <svg class="contact__icon" style="left:-50px; top:2px;" viewBox="0 0 22 22" aria-label="Telephone"><path d="M5 2 L8.5 2 L10 7 L7.8 8.8 C9 11.5 10.5 13 13.2 14.2 L15 12 L20 13.5 L20 17 C20 18.5 18.8 19.5 17 19.5 C9 19 3 13 2.5 5 C2.5 3.2 3.5 2 5 2 Z" fill="#1e1e1e"/><path d="M13 2.5 A6.5 6.5 0 0 1 19.5 9" stroke="#1e1e1e" stroke-width="1.6" fill="none"/><path d="M13 5.5 A3.5 3.5 0 0 1 16.5 9" stroke="#1e1e1e" stroke-width="1.6" fill="none"/></svg>
      020 5194 6281
    </li>
    <li class="contact__item" style="left:404px; top:242px;">
      <svg class="contact__icon" style="left:-56px; top:2px;" viewBox="0 0 22 22" aria-label="Email"><rect x="1" y="4" width="20" height="14" fill="#1e1e1e"/><path d="M1.5 4.5 L11 12 L20.5 4.5" stroke="#77bd43" stroke-width="1.6" fill="none"/></svg>
      TOMASZ@VARKELT.CO.UK
    </li>
    <li class="contact__item" style="left:382px; top:285px;">
      <svg class="contact__icon" style="left:-48px; top:2px;" viewBox="0 0 22 22" aria-label="Website"><circle cx="11" cy="11" r="10" fill="#1e1e1e"/><g stroke="#77bd43" stroke-width="1.2" fill="none"><ellipse cx="11" cy="11" rx="4.2" ry="10"/><line x1="1" y1="11" x2="21" y2="11"/><line x1="11" y1="1" x2="11" y2="21"/><path d="M3 6 H19 M3 16 H19"/></g></svg>
      WWW.VARKELT.CO.UK
    </li>
  </ul>
</section>

<section class="card card--back">
  <div class="services-band"><h2 class="services-band__title">SERVICES</h2></div>
  <ul class="services services--left">
    <li>KITCHEN RENOVATIONS</li>
    <li>BATHROOM RENOVATIONS</li>
    <li>HOUSE RENOVATIONS</li>
    <li>GARAGE CONVERSIONS</li>
    <li>EXTENSIONS</li>
    <li>LOFT CONVERSIONS</li>
    <li>CONSERVATORIES</li>
    <li>CARPENTRY</li>
  </ul>
  <ul class="services services--right">
    <li>TILING</li>
    <li>ELECTRICAL</li>
    <li>PLUMBING &amp; HEATING</li>
    <li>BRICKLAYING</li>
    <li>LANDSCAPING</li>
    <li>DECORATING</li>
    <li>PLASTERING</li>
  </ul>
</section>

</body>
</html>
```